Brivolt Technologies business card design

We need a business card designed with our new logo. it would be great if the card could communicate it is a technology based company.

Target Market(s)

system integrators

Industry/Entity Type

technology, IOT

Contact Information for Business Card

Name, designation, Address, telephone number, email address

Requirements
Must have
• logo and company name
Nice to have
• something to do with technology

```html
<!DOCTYPE html>
<html lang="en">
<head>
<meta charset="utf-8">
<title>Brivolt Technologies – Business Card</title>
<link href="https://fonts.googleapis.com/css2?family=Inter:wght@400;500&display=swap" rel="stylesheet">
<style>
  :root {
    --backdrop: #5a5a5a;
    --card-white: #ffffff;
    --card-dark: #3d3d3d;
    --ink: #3a3a3a;
    --orange: #f7931e;
    --white: #ffffff;
  }
  * { margin: 0; padding: 0; box-sizing: border-box; }
  html, body {
    width: 1135px; height: 1200px; overflow: hidden;
    background: var(--backdrop);
    font-family: "Inter", sans-serif;
  }
  .card {
    position: absolute; left: 205px;
    width: 726px; height: 415px;
  }
  .card--front { top: 145px; background: var(--card-white); }
  .card--back { top: 642px; background: var(--card-dark); }

  .brand {
    position: absolute;
    display: flex; align-items: center; gap: 12px;
    font-weight: 500;
  }
  .brand__square { width: 22px; height: 22px; background: var(--orange); flex: none; }
  .card--front .brand {
    left: 60px; top: 190px;
    color: var(--ink); font-size: 22px;
  }
  .card--back .brand {
    left: 0; right: 0; top: 186px; justify-content: center;
    color: var(--white); font-size: 40px; gap: 18px;
  }
  .card--back .brand__square { width: 34px; height: 34px; }

  .contact { position: absolute; left: 405px; top: 104px; right: 0; color: var(--ink); }
  .contact__name {
    font-size: 28px; font-weight: 500; color: var(--orange);
    letter-spacing: 0.2px; line-height: 1.2;
  }
  .contact__role { font-size: 18px; line-height: 1.2; margin-top: 1px; }
  .contact__rule { height: 1.5px; background: var(--orange); margin: 14px 0 14px; }
  .contact__address { font-size: 18px; line-height: 24px; }
  .contact__list { list-style: none; margin-top: 4px; }
  .contact__item {
    display: flex; align-items: center; gap: 7px;
    font-size: 18px; line-height: 24.5px;
  }
  .contact__icon { width: 13px; height: 13px; flex: none; }
</style>
</head>
<body>
  <section class="card card--front">
    <div class="brand"><span class="brand__square"></span>Brivolt Technologies</div>
    <div class="contact">
      <h1 class="contact__name">DANIEL REINHOLT</h1>
      <p class="contact__role">DIRECTOR</p>
      <div class="contact__rule"></div>
      <p class="contact__address">1472 Alder Lane<br>Fairview, MI 48621</p>
      <ul class="contact__list">
        <li class="contact__item">
          <svg class="contact__icon" viewBox="0 0 16 16" aria-hidden="true"><path d="M4 1.5 L6.5 5 L5 6.5 C6 9 7.5 10.5 9.5 11 L11 9.5 L14.5 12 L13 14.5 C7 14.5 1.5 9 1.5 3 Z" fill="none" stroke="#f7931e" stroke-width="1.6" stroke-linejoin="round"/></svg>
          (555) 318-4072
        </li>
        <li class="contact__item">
          <svg class="contact__icon" viewBox="0 0 16 16" aria-hidden="true"><rect x="1.5" y="3.5" width="13" height="9" fill="none" stroke="#f7931e" stroke-width="1.6"/><path d="M1.5 3.5 L8 9 L14.5 3.5" fill="none" stroke="#f7931e" stroke-width="1.6"/></svg>
          info@brivolttech.com
        </li>
        <li class="contact__item">
          <svg class="contact__icon" viewBox="0 0 16 16" aria-hidden="true"><g fill="none" stroke="#f7931e" stroke-width="1.3"><circle cx="8" cy="8" r="6.5"/><ellipse cx="8" cy="8" rx="3" ry="6.5"/><path d="M1.5 8 H14.5 M2.5 4.8 H13.5 M2.5 11.2 H13.5"/></g></svg>
          brivolttech.com
        </li>
      </ul>
    </div>
  </section>

  <section class="card card--back">
    <div class="brand"><span class="brand__square"></span>Brivolt Technologies</div>
  </section>
</body>
</html>
```